PlayTallyCollective - Game Statistics and Achievement Tracking

I need a new modern design for an existing website.

The website is a project to track statistics and achievements for games (currently Vaporn Achievements/Stats and stats for Cargo Haul Odyssey 2 and Frontier Rig Journeys).
I am currently expanding the site with other platforms (like QVR) and more games.
I am also adding a user registration/signin with user profiles to show off their achievements and stats across all platforms and games.

The current website is available at https://plytly.example/
To search for data you can use the username "pixelornin" (without quotes).

The design should be modern and extendable and contain space for a logo.

The logo should match the project. It should combine Gaming with statistics.

Target Market(s)

Video game players

Number of Pages Required

5+ page

Font styles to use
Sans Serif

Requirements
Must have
• Basic Layout, User profile page (not yet available on live site), Search Page for Platforms/Games, Platform profile page, Dark theme

```html
<!DOCTYPE html>
<html lang="en">
<head>
<meta charset="utf-8">
<title>Game Statistics</title>
<link href="https://fonts.googleapis.com/css2?family=Open+Sans:wght@400;500;600&display=swap" rel="stylesheet">
<style>
:root{
  --bg:#140b1c;
  --bg-deep:#0e0816;
  --bg-plum:#1f1120;
  --red:#e0112b;
  --red-text:#d3112a;
  --white:#ffffff;
  --muted:#cfc8d4;
  --card-text:#111111;
  --card-muted:#666666;
  --line:#4a3a4e;
}
*{margin:0;padding:0;box-sizing:border-box}
html,body{width:1200px;height:3565px;overflow:hidden}
body{font-family:"Open Sans",sans-serif;background:var(--bg);color:var(--white);position:relative}
section,header,footer{position:absolute;left:0;width:1200px}
.abs{position:absolute}
.btn{background:var(--red);color:var(--white);font-weight:600;border-radius:3px;display:flex;align-items:center;justify-content:center;gap:10px}

/* hero */
.hero{top:0;height:616px;background:radial-gradient(ellipse at 50% 55%,#5a1410 0%,#2a0a14 35%,#0f0814 75%),#0f0814}
.hero-art{inset:0;position:absolute;background:radial-gradient(circle at 50% 60%,rgba(255,120,40,.25),transparent 30%),linear-gradient(90deg,rgba(10,20,50,.6),transparent 30%,transparent 70%,rgba(10,20,50,.6))}
.brand{left:91px;top:28px;font-size:30px;font-weight:400}
.nav{left:449px;top:38px;display:flex;gap:20px;font-size:15px}
.signin{left:994px;top:28px;width:115px;height:41px;font-size:15px}
.hero-title{top:196px;width:100%;text-align:center;font-size:52px;font-weight:600}
.hero-sub{top:272px;width:100%;text-align:center;font-size:23px;line-height:38px;color:#f0eaf0}
.search{left:271px;top:383px;width:657px;height:56px;border:2px solid #e8e8e8;border-radius:3px;display:flex;align-items:center;padding:0 6px 0 16px}
.search span{flex:1;margin-left:14px;font-size:15px;color:#e0dbe4}
.search .btn{width:124px;height:40px;font-size:15px}

/* offer */
.offer{top:616px;height:702px;background:radial-gradient(ellipse at 20% 10%,#1e1640,transparent 55%),radial-gradient(ellipse at 10% 90%,#3a0e22,transparent 50%),var(--bg-deep)}
.sec-title{width:100%;text-align:center;font-size:42px;font-weight:500}
.sec-desc{width:100%;text-align:center;font-size:15px;line-height:26px;color:#eee}
.card{top:219px;width:325px;height:400px;background:#fff;border-radius:3px;overflow:hidden;color:var(--card-text)}
.card-img{height:250px}
.card h3{font-size:19px;font-weight:500;margin:14px 17px 6px}
.card p{font-size:13px;line-height:19px;color:var(--card-muted);margin:0 17px}
.card a{display:block;margin:18px 17px;color:var(--red-text);font-size:15px;font-weight:500;text-decoration:none}

/* how */
.how{top:1318px;height:492px;background:linear-gradient(90deg,#15091c,#2a1024 60%)}
.how-text{left:102px;top:100px;width:420px}
.how-text h2{font-size:23px;font-weight:500;margin-bottom:10px}
.how-text h4{font-size:17px;font-weight:500;line-height:27px;margin-bottom:12px}
.how-text p{font-size:14px;line-height:23px;margin-bottom:10px}
.ticks{list-style:none}
.ticks li{display:flex;align-items:center;gap:9px;font-size:14px;line-height:23px}
.dash{left:577px;top:0;width:623px;height:492px;background:linear-gradient(135deg,#1a1430,#2b0f2c 45%,#161228)}

/* content */
.content{top:1810px;height:731px;background:radial-gradient(ellipse at 80% 60%,#3a0f28,transparent 55%),var(--bg)}
.photo{left:96px;top:83px;width:474px;height:517px;background:linear-gradient(160deg,#7c8a8a,#4c5558 45%,#3a2e30)}
.content-col{left:626px;top:139px;width:466px}
.search-light{height:57px;background:#fff;border-radius:3px;display:flex;align-items:center;padding:0 8px 0 16px}
.search-light span{flex:1;margin-left:14px;font-size:15px;color:#b5b5b5}
.search-light .btn{width:124px;height:41px;font-size:15px}
.content-col h2{margin-top:22px;font-size:34px;line-height:48px;font-weight:500}
.content-col p{margin-top:8px;font-size:14px;line-height:21px}
.content-col .ticks{margin-top:14px}
.content-col .ticks li{font-size:15px;line-height:28.5px}

/* projects */
.projects{top:2541px;height:649px;background:var(--bg-plum)}
.tile{border-radius:2px}

/* footer */
.footer{top:3190px;height:375px;background:var(--bg-deep)}
.footer p{left:240px;width:720px;top:136px;text-align:center;font-size:15px;line-height:22px}
.foot-nav{top:209px;width:100%;display:flex;justify-content:center;font-size:15px}
.foot-nav a{color:#ddd;text-decoration:none;padding:0 10px;border-left:1px solid #888}
.foot-nav a:first-child{border-left:none}
.social{top:256px;width:100%;display:flex;justify-content:center;gap:12px}
.social span{width:18px;height:18px;border-radius:50%;background:#fff}
.rule{left:93px;width:1014px;top:298px;height:1px;background:var(--line)}
.copy{top:318px;width:100%;text-align:center;font-size:13px;color:#ddd}
</style>
</head>
<body>

<header class="hero">
  <div class="hero-art" role="img" aria-label="Glowing red and orange sci-fi tunnel background"></div>
  <div class="abs brand">Game Statistics</div>
  <nav class="abs nav"><span>Home</span><span>About Us</span><span>Platforms</span><span>Games</span><span>Leaderboards</span></nav>
  <div class="abs btn signin">Sign In
    <svg width="16" height="16" viewBox="0 0 16 16" fill="none" stroke="#fff" stroke-width="1.6"><path d="M9 2h4v12H9M2 8h8M7 5l3 3-3 3"/></svg>
  </div>
  <h1 class="abs hero-title">Your Gaming Stats Unified.</h1>
  <div class="abs hero-sub">Rack Achievements, Milestones, And Gaming Progress Across<br>Vaporn, QVR, And More!</div>
  <div class="abs search">
    <svg width="22" height="22" viewBox="0 0 22 22" fill="none" stroke="#fff" stroke-width="2"><circle cx="9" cy="9" r="7"/><path d="M14 14l6 6"/></svg>
    <span>Search your username or platform...</span>
    <div class="btn">Get Started</div>
  </div>
</header>

<section class="offer">
  <h2 class="abs sec-title" style="top:70px">What We Offer</h2>
  <p class="abs sec-desc" style="top:131px">Track Your Achievements, Compare With Friends, And Explore Your Gaming Progress<br>Across Multiple Platforms With Our Comprehensive Services.</p>
  <article class="abs card" style="left:83px">
    <div class="card-img" role="img" aria-label="Player at a monitor showing a victory screen" style="background:linear-gradient(135deg,#2a4a70,#1a2436 50%,#6a4a30)"></div>
    <h3>Achievement Tracking &amp; Stats</h3>
    <p>Users Can Link Their Gaming Accounts (Vaporn, QVR, Boxline, Etc.) To Track Their Achievements, Compare Stats...</p>
    <a>read more &nbsp;»</a>
  </article>
  <article class="abs card" style="left:437px">
    <div class="card-img" role="img" aria-label="Colourful glowing cubes on a dark surface" style="background:radial-gradient(circle at 50% 45%,#c79a3a,#3a3a2a 40%,#1a1a1a)"></div>
    <h3>Achievement Tracking &amp; Stats</h3>
    <p>Users Can Link Their Gaming Accounts (Vaporn, QVR, Boxline, Etc.) To Track Their Achievements, Compare Stats...</p>
    <a>read more &nbsp;»</a>
  </article>
  <article class="abs card" style="left:792px">
    <div class="card-img" role="img" aria-label="Player with headphones in front of a bright monitor" style="background:linear-gradient(135deg,#c7cfd8,#d88a6a 45%,#e8e8ea)"></div>
    <h3>Achievement Tracking &amp; Stats</h3>
    <p>Users Can Link Their Gaming Accounts (Vaporn, QVR, Boxline, Etc.) To Track Their Achievements, Compare Stats...</p>
    <a>read more &nbsp;»</a>
  </article>
</section>

<section class="how">
  <div class="abs how-text">
    <h2>How It Works</h2>
    <h4>Easily Connect Your Gaming Accounts, Track Your Progress, And Explore Detailed Stats And Achievements!</h4>
    <p>Get Started By Creating An Account And Linking Your Gaming Profiles. Track Your Achievements And Explore Detailed Stats Across Popular Platforms Like Vaporn, QVR, And Boxline.</p>
    <ul class="ticks">
      <li><svg width="14" height="12" viewBox="0 0 14 12" fill="none" stroke="#e0112b" stroke-width="2"><path d="M1 6l4 4 8-9"/></svg>create an account or sign in</li>
      <li><svg width="14" height="12" viewBox="0 0 14 12" fill="none" stroke="#e0112b" stroke-width="2"><path d="M1 6l4 4 8-9"/></svg>connect your gaming accounts</li>
      <li><svg width="14" height="12" viewBox="0 0 14 12" fill="none" stroke="#e0112b" stroke-width="2"><path d="M1 6l4 4 8-9"/></svg>track achievements and stats</li>
      <li><svg width="14" height="12" viewBox="0 0 14 12" fill="none" stroke="#e0112b" stroke-width="2"><path d="M1 6l4 4 8-9"/></svg>join the community</li>
    </ul>
  </div>
  <div class="abs dash" role="img" aria-label="Illustrated neon gaming stats dashboard with menus and icons"></div>
</section>

<section class="content">
  <div class="abs photo" role="img" aria-label="Hands holding a phone game controller with cups in the background"></div>
  <div class="abs content-col">
    <div class="search-light">
      <svg width="22" height="22" viewBox="0 0 22 22" fill="none" stroke="#bbb" stroke-width="2"><circle cx="9" cy="9" r="7"/><path d="M14 14l6 6"/></svg>
      <span>Search your username or platform...</span>
      <div class="btn">Get Started</div>
    </div>
    <h2>As Opposed To Using Content Here, Content Here Making</h2>
    <p>Less Normal Distribution Of Letters, As Opposed To Using 'Content Here, Content Here', Making It Look Like Readable English. Many Desktop Publishing Packages And Web Page Editors Now Use Lorem Ipsum As Their Default Model Text, And A Search</p>
    <ul class="ticks">
      <li><svg width="14" height="12" viewBox="0 0 14 12" fill="none" stroke="#e0112b" stroke-width="2"><path d="M1 6l4 4 8-9"/></svg>lorem ipsum is that it has a more</li>
      <li><svg width="14" height="12" viewBox="0 0 14 12" fill="none" stroke="#e0112b" stroke-width="2"><path d="M1 6l4 4 8-9"/></svg>lorem ipsum is that it has a more</li>
      <li><svg width="14" height="12" viewBox="0 0 14 12" fill="none" stroke="#e0112b" stroke-width="2"><path d="M1 6l4 4 8-9"/></svg>lorem ipsum is that it has a more</li>
      <li><svg width="14" height="12" viewBox="0 0 14 12" fill="none" stroke="#e0112b" stroke-width="2"><path d="M1 6l4 4 8-9"/></svg>lorem ipsum is that it has a more</li>
      <li><svg width="14" height="12" viewBox="0 0 14 12" fill="none" stroke="#e0112b" stroke-width="2"><path d="M1 6l4 4 8-9"/></svg>lorem ipsum is that it has a more</li>
    </ul>
  </div>
</section>

<section class="projects">
  <h2 class="abs sec-title" style="top:50px">Our Recent Projects</h2>
  <p class="abs sec-desc" style="top:112px">Lorem Ipsum as their default model text, and a search for 'lorem<br>ipsum' will uncover many infancy.</p>
  <div class="abs tile" role="img" aria-label="Office with rows of gaming desks" style="left:112px;top:192px;width:318px;height:186px;background:linear-gradient(135deg,#5a5a58,#2a2624 60%,#7a2a20)"></div>
  <div class="abs tile" role="img" aria-label="Player at a blue-lit gaming setup" style="left:453px;top:192px;width:318px;height:186px;background:linear-gradient(135deg,#1a5a8a,#1a2438 50%,#8a2a20)"></div>
  <div class="abs tile" role="img" aria-label="Person standing in a gaming room" style="left:793px;top:192px;width:294px;height:186px;background:linear-gradient(135deg,#bcc4cc,#4a4a5a 60%,#2a2a30)"></div>
  <div class="abs tile" role="img" aria-label="Monitor showing a colourful game scene" style="left:112px;top:406px;width:205px;height:185px;background:linear-gradient(135deg,#2a3a5a,#4a3a7a 50%,#1a1a28)"></div>
  <div class="abs tile" role="img" aria-label="Players at a gaming event with red lighting" style="left:339px;top:406px;width:335px;height:185px;background:linear-gradient(135deg,#3a1a1a,#2a2a2a 50%,#4a6a3a)"></div>
  <div class="abs tile" role="img" aria-label="Hands holding a game controller" style="left:696px;top:406px;width:391px;height:185px;background:linear-gradient(135deg,#2a2022,#3a2a2a 50%,#1a1416)"></div>
</section>

<footer class="footer">
  <h2 class="abs sec-title" style="top:72px;font-size:32px">Game Statistics</h2>
  <p class="abs">lorem ipsum is that it has a more-or-less normal distribution of letters, as opposed to using 'content here, content here', making it look like readable english. many desktop publishing packages and web page editors now use lorem ipsum as their default model text, and a search for</p>
  <nav class="abs foot-nav"><a>Home</a><a>About Us</a><a>Platforms</a><a>Games</a><a>Leaderboards</a></nav>
  <div class="abs social">
    <span role="img" aria-label="Professional network"></span>
    <span role="img" aria-label="Social network"></span>
    <span role="img" aria-label="Photo sharing network"></span>
  </div>
  <div class="abs rule"></div>
  <div class="abs copy">© 2024 Play-Tally-Collective</div>
</footer>

</body>
</html>
```